Business cards for Norwegian software consultancy business

We are in need of business cards for our Norwegian consultancy company.
“Valto Brindex AS” specializes in software development, architecture and agile methodology, providing mostly on-site services at customers.
The cards should reflect a certain level of business professionalism with an elegant touch, while paying tribute to our modern and technological heritage. Our logo should be featured, as well as room for basic information about the cardholder and legal information of the company (company name, address and VAT number).
We would like our cards to reflect that we are a modern consulting company. It should present a professional image that people will remember. The texture and color pallette should reflect our professionalism and reliability, so we prefer a light color pallette with colors such as gray, white, blue and black. The number of colors used should however not be overwhelming, with the text being distinct and readable.
We are open to untraditional layouts and playful designs as long as they communicate the intent stated above.
You could also take a look at our website http://www.brindex.no for input on our visual profile.
Our logo is attached in the form of vectors and rasterized PNG. Please comment if you would like the black-white and/or inverted versions as well.
Industry/Entity Type
Architecture
Contact Information for Business Card
Company information:
Valto Brindex AS
Kvernlia 14, 3170 Sem
482 71 519
info@brindex.no
www.brindex.no
Employee information:
Full name
Title
Email
Phone
Font styles to use
Look and feel

```html
<!DOCTYPE html>
<html lang="en">
<head>
<meta charset="utf-8">
<title>Valto Brindex AS – Business Cards</title>
<link href="https://fonts.googleapis.com/css2?family=Michroma&family=Arimo:wght@400;700&family=Lato:ital,wght@0,700;1,400&display=swap" rel="stylesheet">
<style>
  :root {
    --backdrop: #2a2a2c;
    --card-white: #f7f7f7;
    --card-dark: #333335;
    --brand-blue: #3e8fcb;
    --ink: #1d1d1f;
    --ink-soft: #444;
    --on-dark: #f0f0f0;
    --on-dark-muted: #bdbdbd;
  }
  * { box-sizing: border-box; margin: 0; padding: 0; }
  html, body { width: 1200px; height: 873px; overflow: hidden; }
  body {
    background: var(--backdrop);
    display: flex;
    align-items: center;
    justify-content: center;
    gap: 40px;
    font-family: "Arimo", Arial, sans-serif;
  }
  .card {
    position: relative;
    width: 540px;
    height: 310px;
    border-radius: 22px;
    overflow: hidden;
    box-shadow: 0 14px 30px rgba(0,0,0,.45);
  }

  /* Back of card */
  .card--back { background: linear-gradient(160deg, #3b3b3e, var(--card-dark) 60%, #2c2c2e); }
  .back-brand { position: absolute; right: 60px; top: 96px; text-align: right; }
  .back-brand__tagline {
    font-family: "Lato", serif; font-style: italic; font-size: 11px;
    color: var(--on-dark-muted); margin-bottom: 6px;
  }
  .brand-name {
    display: flex; align-items: center; gap: 12px;
    font-family: "Michroma", sans-serif; font-size: 30px; letter-spacing: 1px;
  }
  .brand-name__mark { width: 22px; height: 22px; background: var(--brand-blue); flex: none; }
  .card--back .brand-name { color: var(--on-dark); }
  .back-services {
    position: absolute; left: 0; right: 0; bottom: 34px; text-align: center;
    font-family: "Lato", sans-serif; font-weight: 700; font-size: 14px; color: var(--on-dark);
  }

  /* Front of card */
  .card--front { background: var(--card-white); }
  .card--front .brand-name { color: var(--ink); font-size: 26px; }
  .front-brand { position: absolute; top: 34px; left: 0; right: 0; display: flex; justify-content: center; }

  .holder { position: absolute; right: 0; top: 104px; text-align: right; }
  .holder__name {
    font-family: "Michroma", sans-serif; font-size: 15px; color: var(--brand-blue);
    padding-right: 24px;
  }
  .holder__title { font-size: 12px; color: var(--ink-soft); margin-top: 6px; padding-right: 24px; }
  .holder__band { margin-top: 6px; height: 3px; width: 230px; margin-left: auto; background: var(--brand-blue); }
  .holder__vat {
    display: inline-block; margin-right: 12px;
    background: var(--brand-blue); color: #fff; font-size: 12px;
    padding: 4px 16px; border-radius: 0 0 12px 12px;
  }

  .company { position: absolute; left: 0; top: 150px; }
  .company__pill {
    display: inline-block; margin-left: 16px;
    background: var(--brand-blue); color: var(--ink);
    font-family: "Michroma", sans-serif; font-size: 11px;
    padding: 5px 16px; border-radius: 12px 12px 0 0;
  }
  .company__band { height: 3px; width: 250px; background: var(--brand-blue); }
  .contact-list { list-style: none; margin: 8px 0 0 22px; }
  .contact-list li {
    display: flex; align-items: center; gap: 10px;
    font-size: 12.5px; color: var(--ink); height: 19px;
  }
  .contact-list svg { width: 13px; height: 13px; flex: none; }
  .company__address {
    margin: 10px 0 0 22px; white-space: nowrap;
    font-family: "Michroma", sans-serif; font-size: 10.5px; color: var(--brand-blue);
  }
</style>
</head>
<body>

  <section class="card card--back" aria-label="Business card, back">
    <div class="back-brand">
      <p class="back-brand__tagline">Development &amp; IT Services</p>
      <div class="brand-name"><span class="brand-name__mark"></span>Valto Brindex</div>
    </div>
    <p class="back-services">Software Development, Project Management &amp; IT Operations</p>
  </section>

  <section class="card card--front" aria-label="Business card, front">
    <div class="front-brand">
      <div class="brand-name"><span class="brand-name__mark"></span>Valto Brindex</div>
    </div>

    <div class="holder">
      <p class="holder__name">Henrik Solvang</p>
      <p class="holder__title">Owner / Founder</p>
      <div class="holder__band"></div>
      <span class="holder__vat">VAT 917 604 238</span>
    </div>

    <div class="company">
      <span class="company__pill">VALTO BRINDEX AS</span>
      <div class="company__band"></div>
      <ul class="contact-list">
        <li>
          <svg viewBox="0 0 14 14" aria-hidden="true"><rect x="3" y="1" width="8" height="12" rx="1.5" fill="none" stroke="#3e8fcb" stroke-width="1.4"/></svg>
          +47 482 71 519
        </li>
        <li>
          <svg viewBox="0 0 14 14" aria-hidden="true"><rect x="1" y="3" width="12" height="8" fill="#3e8fcb"/><path d="M1 3l6 5 6-5" fill="none" stroke="#fff" stroke-width="1"/></svg>
          info@brindex.no
        </li>
        <li>
          <svg viewBox="0 0 14 14" aria-hidden="true"><path d="M6 8l2-2M5 6.5L3 8.5a2 2 0 0 0 2.8 2.8L7.5 9.5M9 7.5l2-2a2 2 0 0 0-2.8-2.8L6.5 4.5" fill="none" stroke="#3e8fcb" stroke-width="1.4" stroke-linecap="round"/></svg>
          www.brindex.no
        </li>
      </ul>
      <p class="company__address">Kvernlia 14, 3170 Sem, Norway</p>
    </div>
  </section>

</body>
</html>
```